Health Care Company with Logo Needs Business Cards designed

We are a luxury behavioral health company looking for business cards design we already have a logo and are looking for someone to design a sophisticated luxurious looking business card. Please note that Card design should be captivating just like the logo and also encompass the logo color

Industry/Entity Type

Healthcare

Contact Information for Business Card

Logo,company name, tagline, my name and title, contact details, and physical address

```html
<!DOCTYPE html>
<html lang="en">
<head>
<meta charset="utf-8">
<title>Corvin Behavioral Health – Business Card</title>
<link rel="stylesheet" href="https://fonts.googleapis.com/css2?family=Arimo:wght@400;700&display=swap">
<style>
  :root {
    --page-bg: #d9d2c8;
    --card-purple-core: #6b2a8c;
    --card-purple: #552068;
    --card-purple-deep: #32123c;
    --text-cream: #f1e6d6;
    --accent-blue: #1687cf;
    --contact-tan: #bba894;
    --icon-teal: #1d5f78;
    --area-orange: #cf6a12;
    --area-blue: #0a6fae;
    --area-green: #4f7d1c;
  }
  * { margin: 0; padding: 0; box-sizing: border-box; }
  html, body {
    width: 1200px; height: 927px; overflow: hidden;
    background: var(--page-bg);
  }
  .business-card {
    position: absolute; left: 151px; top: 214px;
    width: 894px; height: 499px; overflow: hidden;
    background: radial-gradient(ellipse 420px 340px at 270px 200px, var(--card-purple-core) 0%, var(--card-purple) 55%, var(--card-purple-deep) 100%);
    box-shadow: 0 10px 30px rgba(0,0,0,0.25);
    font-family: "Arimo", Arial, sans-serif;
  }
  .company-name {
    position: absolute; left: 55px; top: 44px;
    font-weight: 700; font-size: 31px;
    color: var(--text-cream); white-space: nowrap;
  }
  .company-tagline {
    position: absolute; left: 55px; top: 86px;
    font-weight: 400; font-size: 14px; letter-spacing: 0.5px;
    color: var(--accent-blue); white-space: nowrap;
  }
  .person-name {
    position: absolute; left: 55px; top: 146px;
    font-weight: 700; font-size: 31px; color: var(--accent-blue);
  }
  .person-title {
    position: absolute; left: 55px; top: 187px;
    font-size: 22px; color: var(--text-cream);
  }
  .postal-address {
    position: absolute; left: 55px; top: 258px;
    font-style: normal; font-size: 22px; line-height: 31px;
    color: var(--text-cream);
  }
  .contact-list {
    position: absolute; left: 55px; top: 346px; list-style: none;
  }
  .contact-item {
    display: flex; align-items: center; height: 31px;
    font-size: 23px; color: var(--contact-tan);
  }
  .contact-icon { width: 20px; height: 20px; margin-right: 15px; flex: none; }
  .brand-colour-area {
    position: absolute; left: 520px; top: 0; width: 374px; height: 499px;
    background: linear-gradient(160deg, var(--area-orange) 0%, var(--area-blue) 45%, var(--area-green) 70%, var(--card-purple-deep) 100%);
    opacity: 0.85;
  }
</style>
</head>
<body>
  <article class="business-card">
    <div class="company-name">Corvin Behavioral Health</div>
    <div class="company-tagline">Calm care for lasting renewal</div>

    <h1 class="person-name">Daniel Reeves</h1>
    <div class="person-title">Manager</div>

    <address class="postal-address">Your address, city<br>state, ZIP 0000</address>

    <ul class="contact-list">
      <li class="contact-item">
        <svg class="contact-icon" viewBox="0 0 24 24" aria-hidden="true"><path fill="var(--icon-teal)" d="M6.6 10.8a15.1 15.1 0 0 0 6.6 6.6l2.2-2.2a1 1 0 0 1 1-.25 11.4 11.4 0 0 0 3.6.57 1 1 0 0 1 1 1V20a1 1 0 0 1-1 1A17 17 0 0 1 3 4a1 1 0 0 1 1-1h3.5a1 1 0 0 1 1 1c0 1.25.2 2.45.57 3.57a1 1 0 0 1-.25 1z"/></svg>
        555-014-7382
      </li>
      <li class="contact-item">
        <svg class="contact-icon" viewBox="0 0 24 24" aria-hidden="true"><rect x="2" y="5" width="20" height="14" rx="1.5" fill="none" stroke="var(--icon-teal)" stroke-width="2"/><path d="M3 6l9 7 9-7" fill="none" stroke="var(--icon-teal)" stroke-width="2"/></svg>
        youremail@mailbox.com
      </li>
      <li class="contact-item">
        <svg class="contact-icon" viewBox="0 0 24 24" aria-hidden="true"><g fill="none" stroke="var(--icon-teal)" stroke-width="1.8"><circle cx="12" cy="12" r="10"/><ellipse cx="12" cy="12" rx="4.5" ry="10"/><path d="M2 12h20M4 7h16M4 17h16"/></g></svg>
        www.yourwebsite.com
      </li>
    </ul>

    <div class="brand-colour-area" role="img" aria-label="Large brand symbol area in orange, blue, green and purple"></div>
  </article>
</body>
</html>
```